Letterhead Design for Law Firm

**Edit: I have added the photo of a bottom that I like.

------
We are looking for a re-design of our new letterhead. The letterhead is for a law firm and will be used for digital and traditionally printed correspondence.

Here are some suggestions:

- Please use colours are #8ec900 and simple black.
- Please do not use any type of "waves" at the bottom of the page. This is not in style at all.
- Please stay modern yet conservative.
- Please use font Segoe UI Light or similar if you can
- Avoid clipart or illustrations.
- Utilize ample white space in the layout so the design looks clean and information is easy to read at a glance. Don't overcrowd the letterhead.
- Make sure the letterhead design is consistent with our brand identity (see corvelith.ca)
-Please, no black headers or footers.

I am attaching my current letterhead and signature for your convenience.

Remember, the letterhead is an extension of our professional identity. We are a successful firm and trial lawyers who correspond with insurers, judges, lawyers, courts, clients, etc. Make it new, modern, attractive, yet powerful and conservative.

It needs to be easily printable. I would like the bleed removed in print so the black bar the bottom crosses the page (but the text is not near the edges)
Updates

Low design quality

Target Market(s)

Clients, Government Offices, Judiciary, Lawyers, Insurance Companies, Colleagues.

Industry/Entity Type

Law

Other font styles liked:
• Segoe UI LIght, Calibri Light,

Colors
00AB8E
00BBA5
67D7C9
C6EFE9
E9F9F6

Requirements
Must have
• Everything that is on the letterhead now.
Nice to have
• Cutting Edge design, yet conservative.
Should not have
• law firm cliche design, images,

```html
<!DOCTYPE html>
<html lang="en">
<head>
<meta charset="utf-8">
<title>Corvelith Letterhead</title>
<link rel="stylesheet" href="https://fonts.googleapis.com/css2?family=Arimo:wght@400;700&family=Mulish:wght@600;700&family=Oswald:wght@500&display=swap">
<style>
  :root {
    --brand-green: #8ec900;
    --ink: #000000;
    --text: #555555;
    --rule: #6a6a6a;
    --paper: #ffffff;
    --backdrop: #dcdcdc;
  }
  * { box-sizing: border-box; margin: 0; padding: 0; }
  html, body {
    width: 1189px; height: 1200px; overflow: hidden;
    background: var(--backdrop);
  }
  .letterhead {
    position: absolute; left: 170px; top: 0;
    width: 848px; height: 1200px;
    background: var(--paper);
    font-family: "Arimo", Arial, sans-serif;
    color: var(--text);
  }
  .firm-name {
    position: absolute; left: 64px; top: 58px;
    font-family: "Oswald", "Arial Narrow", sans-serif;
    font-weight: 500; font-size: 46px; letter-spacing: 2px;
    color: var(--ink); line-height: 1;
  }
  .contact {
    position: absolute; left: 582px; top: 52px;
    font-size: 12.5px; line-height: 16.3px;
  }
  .contact .phone { display: flex; align-items: center; gap: 4px; margin-bottom: 4px; }
  .contact svg { width: 10px; height: 10px; }
  .header-rule {
    position: absolute; left: 64px; top: 134px;
    width: 719px; height: 1px; background: var(--rule);
  }
  .salutation {
    position: absolute; left: 77px; top: 368px;
    font-family: "Mulish", "Century Gothic", sans-serif;
    font-weight: 700; font-size: 19.5px; color: var(--text);
  }
  .body-copy {
    position: absolute; left: 76px; top: 425px; width: 700px;
    font-size: 14px; line-height: 17.5px;
  }
  .body-copy p { margin-bottom: 15px; }
  .closing {
    position: absolute; left: 77px; top: 786px;
    font-family: "Mulish", "Century Gothic", sans-serif;
    font-weight: 700; font-size: 11px;
  }
  .signature {
    position: absolute; left: 502px; top: 885px;
    width: 256px; height: 60px;
    background: linear-gradient(90deg, #ececec, #f6f6f6);
  }
  .signatory {
    position: absolute; left: 503px; top: 962px;
    font-size: 12.5px; line-height: 16px;
  }
  .signatory .name { color: var(--brand-green); font-weight: 700; }
  .footer-band { position: absolute; left: 0; bottom: 0; width: 848px; height: 25px; }
  .web-address {
    position: absolute; right: 49px; bottom: 5px;
    color: var(--paper); font-size: 13px; letter-spacing: 2.4px;
  }
</style>
</head>
<body>
  <main class="letterhead">
    <header>
      <div class="firm-name">CORVELITH</div>
      <address class="contact" style="font-style:normal">
        <div class="phone">
          <svg viewBox="0 0 24 24" aria-hidden="true"><path fill="#8ec900" d="M6.6 10.8a15.1 15.1 0 0 0 6.6 6.6l2.2-2.2a1 1 0 0 1 1-.25 11.4 11.4 0 0 0 3.6.57 1 1 0 0 1 1 1V20a1 1 0 0 1-1 1A17 17 0 0 1 3 4a1 1 0 0 1 1-1h3.5a1 1 0 0 1 1 1c0 1.25.2 2.45.57 3.57a1 1 0 0 1-.25 1z"/></svg>
          <span>555-014-2760</span>
        </div>
        <div>48 Alder Row East</div>
        <div>Suite 920</div>
        <div>Brantmoor, ON K0X 2Z9, Canada</div>
      </address>
      <div class="header-rule"></div>
    </header>

    <h1 class="salutation">Dear Mr. Halbrook,</h1>

    <section class="body-copy">
      <p>Lorem ipsum dolor sit amet, consectetuer adipiscing elit, sed diam nonmmy nibh euismod tincidunt ut laor eet dolore magna aliquam erat volutpat. Ut wisi enim ad minim veniam, quis nostrud exerci tationmcorper suscipit lobortis nisl ut aliquip ex ea commodo consequat. Duis autem vel eum iriure dolor in hendrerit in vulputate velit esse molestie consequat, vel illum dolore eu feugiat</p>
      <p>Rorem ipsum dolor sit amet, consectetuer adipiscing elit, sed diam nonmmy nibh euismod tincidunt ut laor eet dolore magna aliquam erat volutpat. Ut wisi enim ad minim veniam, quis nostrud exerci tationmcorper suscipit lobortis nisl ut aliquip ex ea commodo consequat. Duis autem vel eum iriure dolor in hendrerit in vulputate velit esse molest</p>
      <p>Dorem ipsum dolor sit amet, consectetuer adipiscing elit, sed diam nonmmy nibh euismod tincidunt ut laor eet dolore magna aliquam erat volutpat. Ut wisi enim ad minim veniam, quis nostrud exerci tationmcorper suscipit lobortis nisl ut aliquip ex ea commodo consequat. Duis autem vel eum iriure dolor in hendrerit in suscipit lobortis nisl ut aliquip ex ea commodo consequat. Duis autem vel eum iriure dolor in hendrerit in vulputate velit esse molestie consequat, vel illum</p>
      <p>Sorem ipsum dolor sit amet, consectetuer adipiscing elit, sed diam nonmmy nibh euismod tincidunt ut laor eet dolore magna aliquam erat volutpat. Ut wisi enim ad minim veniam, quis nostrud exerci tationmcorper suscipit lobortis nisl ut aliquip ex ea commodo consequat. Duis autem vel eum iriure dolor in</p>
    </section>

    <div class="closing">Sincerely,</div>
    <div class="signature" role="img" aria-label="Handwritten signature of the signing lawyer"></div>
    <div class="signatory">
      <div class="name">Dana M. Corvelith</div>
      <div>Corvelith Law Professional Corporation</div>
    </div>

    <footer>
      <svg class="footer-band" viewBox="0 0 848 25" preserveAspectRatio="none" aria-hidden="true">
        <polygon points="0,13 584,13 576,25 0,25" fill="#000000"/>
        <polygon points="590,0 848,0 848,25 575,25" fill="#8ec900"/>
      </svg>
      <div class="web-address">www.corvelith.ca</div>
    </footer>
  </main>
</body>
</html>
```